Design a Travel and Tourism website

We would like a freelancer to design a website that is essentially easy to use and navigate database providing local information for Travelers about destination countries.

We proposed website would discuss different rates, fees, visa requirement, resort locations, cheap flights, etc. This website should be elegant and modern. Our business name is rovanix.
Some reference websites are zemplorift.ca, brindlefoxhaven.com,
There should be a forum in the website where travell\ers discuss about their first hand tranvel experience to such destinations.

Tourism

```html
<!DOCTYPE html>
<html lang="en">
<head>
<meta charset="utf-8">
<title>Rovanix — Travel and Tourism</title>
<link href="https://fonts.googleapis.com/css2?family=Lato:wght@400;700;900&family=Open+Sans:wght@400;600;700&display=swap" rel="stylesheet">
<style>
:root{
  --orange:#e8600c;
  --orange-dark:#c94f05;
  --ink:#222;
  --text:#444;
  --muted:#666;
  --white:#fff;
  --field:#e6e6e6;
  --panel:rgba(18,18,20,.82);
  --soft:#ececec;
  --footer:#f2f2f2;
  --deals:#1c1e22;
}
*{box-sizing:border-box;margin:0;padding:0}
html,body{width:1200px;height:3030px;overflow:hidden}
body{font-family:"Open Sans",Arial,sans-serif;color:var(--text);background:var(--white);position:relative}
.abs{position:absolute}
svg{display:block}

/* header */
.site-header{position:absolute;left:0;top:0;width:1200px;height:121px;background:var(--white)}
.brand{position:absolute;left:97px;top:48px;display:flex;align-items:center;gap:12px;font-family:"Open Sans",sans-serif;font-weight:700;font-size:28px;color:var(--orange);letter-spacing:.5px}
.brand-dot{width:26px;height:26px;border-radius:50%;background:var(--orange)}
.utility{position:absolute;left:506px;top:30px;display:flex;align-items:center;gap:16px;font-size:13px;color:var(--ink)}
.utility .sep{color:#999}
.utility span.item{display:flex;align-items:center;gap:6px}
.call{position:absolute;left:836px;top:22px;display:flex;align-items:center;gap:12px;font-size:16px;font-weight:600;color:var(--ink)}
.call b{color:var(--orange);font-size:22px;font-weight:600}
.call-icon{width:38px;height:38px;border-radius:50%;background:var(--orange);display:flex;align-items:center;justify-content:center}
.main-nav{position:absolute;right:100px;top:80px;display:flex;gap:36px;font-size:15px;font-weight:600;color:var(--ink)}
.main-nav .active{color:var(--orange)}

/* hero */
.hero{position:absolute;left:0;top:121px;width:1200px;height:649px;background:linear-gradient(180deg,#3a4d63 0%,#2d3340 35%,#3b2f24 70%,#6a4a1c 88%,#2a1d10 100%)}
.search-panel{position:absolute;left:99px;top:47px;width:1002px;height:553px;background:var(--panel)}
.tabs{position:absolute;left:32px;top:26px;display:flex;gap:14px}
.tab{height:44px;padding:0 14px;background:#4b4d52;color:var(--white);font-size:15px;display:flex;align-items:center;gap:10px;border:1px solid #666;white-space:nowrap}
.tab.active{background:var(--orange);border-color:var(--orange)}
.tab-rule{position:absolute;left:32px;top:74px;width:938px;height:2px;background:#8a8a8a}
.subtabs{position:absolute;left:32px;top:105px;width:938px;height:48px;background:#4c4e53;display:flex}
.subtab{padding:0 20px;display:flex;align-items:center;color:var(--white);font-size:15px;font-weight:600;border-right:1px solid #888}
.subtab.active{background:var(--orange);border:none;width:144px;justify-content:center}
.field-label{position:absolute;color:var(--white);font-size:16px;font-weight:600}
.field{position:absolute;height:44px;background:var(--field);border-radius:2px;display:flex;align-items:center;gap:8px;padding:0 12px;color:#555;font-size:14px}
.select{position:absolute;height:44px;background:var(--field);border-radius:2px;display:flex;align-items:center;justify-content:space-between;padding:0 12px;color:#333;font-size:14px}
.check{position:absolute;left:32px;top:370px;display:flex;align-items:center;gap:12px;color:var(--white);font-size:15px;font-weight:600}
.check i{width:13px;height:13px;background:var(--white);display:block}
.btn-search{position:absolute;left:32px;top:480px;width:166px;height:45px;background:var(--orange);color:var(--white);font-size:15px;font-weight:600;display:flex;align-items:center;justify-content:center}
.save-note{position:absolute;left:218px;top:492px;color:var(--white);font-size:17px;font-weight:600}
.panel-rule{position:absolute;left:32px;top:550px;width:970px;height:3px;background:var(--orange)}

/* welcome */
.welcome{position:absolute;left:0;top:770px;width:1200px;height:408px;background:var(--white)}
.section-title{font-family:"Lato",sans-serif;font-weight:700;font-size:28px;color:var(--orange);letter-spacing:.3px}
.welcome .section-title{position:absolute;left:99px;top:52px}
.welcome .lead{position:absolute;left:99px;top:103px;font-size:15px;color:var(--ink)}
.welcome .copy{position:absolute;left:99px;width:660px;font-size:12.5px;line-height:22px;color:var(--text)}
.btn{position:absolute;height:40px;display:flex;align-items:center;justify-content:center;font-size:14px;font-weight:700}
.btn-primary{background:var(--orange);color:var(--white)}
.btn-outline{border:2px solid var(--ink);color:var(--ink);background:var(--white)}
.luggage{position:absolute;left:778px;top:119px;width:343px;height:192px;border-radius:20px;background:linear-gradient(120deg,#f07a1a 0%,#f6a21c 45%,#9bcc2a 70%,#f2c20e 100%)}

/* deals */
.deals{position:absolute;left:0;top:1178px;width:1200px;height:590px;background:linear-gradient(180deg,#2a2d33 0%,var(--deals) 60%,#17181b 100%)}
.deals .title{position:absolute;left:0;width:1200px;top:54px;text-align:center;font-family:"Lato",sans-serif;font-weight:700;font-size:28px;color:var(--white)}
.deals .sub{position:absolute;left:0;width:1200px;top:104px;text-align:center;font-size:15px;color:var(--white)}
.arrow-btn{position:absolute;top:70px;width:40px;height:40px;border-radius:50%;border:2px solid var(--white)}
.deal{position:absolute;top:175px;width:242px}
.deal-photo{height:215px;border:2px solid var(--white);position:relative}
.deal-label{position:absolute;left:0;right:0;bottom:0;height:42px;display:flex;align-items:center;justify-content:center;color:var(--white);font-size:15px;font-weight:700;background:rgba(30,30,30,.78)}
.deal-label.hot{background:var(--orange)}
.deal-text{margin-top:20px;text-align:center;color:var(--white);font-size:12px;line-height:15px}
.deal-foot{margin-top:20px;display:flex;align-items:center;justify-content:center;gap:24px}
.stars{color:var(--white);font-size:14px;letter-spacing:1px}
.book{width:98px;height:34px;border:1.5px solid var(--white);color:var(--white);font-size:12px;display:flex;align-items:center;justify-content:center}
.book.hot{background:var(--orange);border-color:var(--orange)}

/* destinations */
.destinations{position:absolute;left:0;top:1768px;width:1200px;height:551px;background:var(--soft)}
.center-title{position:absolute;left:0;width:1200px;text-align:center}
.center-sub{position:absolute;left:0;width:1200px;text-align:center;font-size:15px;color:var(--ink)}
.tile{position:absolute;width:188px;height:141px;color:var(--white);text-align:center}
.tile h3{margin-top:38px;font-family:"Open Sans",sans-serif;font-weight:700;font-size:21px}
.tile p{font-size:15px;font-weight:600;margin-top:2px}

/* why */
.why{position:absolute;left:0;top:2319px;width:1200px;height:352px;background:var(--white)}
.feature{position:absolute;top:190px;display:flex;gap:14px}
.feature-icon{width:97px;height:97px;border-radius:50%;display:flex;align-items:center;justify-content:center;flex:none}
.feature h4{font-size:17px;font-weight:600;color:var(--ink);margin-top:8px}
.feature p{font-size:12px;line-height:17px;color:var(--muted);width:190px;margin-top:8px}

/* footer */
.site-footer{position:absolute;left:0;top:2671px;width:1200px;height:359px;background:var(--footer);border-top:3px solid var(--orange)}
.footer-brand{position:absolute;left:0;width:1200px;top:64px;display:flex;justify-content:center;align-items:center;gap:12px;font-weight:700;font-size:28px;color:var(--orange)}
.contact-row{position:absolute;top:150px;left:0;width:1200px;display:flex;justify-content:center;gap:36px;font-size:19px;color:var(--ink)}
.contact-row span{display:flex;align-items:center;gap:12px}
.ring{width:36px;height:36px;border-radius:50%;border:2px solid var(--ink);display:flex;align-items:center;justify-content:center}
.footer-nav{position:absolute;top:229px;left:0;width:1200px;display:flex;justify-content:center;gap:26px;font-size:14px;font-weight:600;color:var(--ink)}
.footer-rule{position:absolute;left:99px;top:281px;width:1002px;height:1px;background:#555}
.copyright{position:absolute;left:99px;top:310px;font-size:14px;color:var(--ink)}
.social{position:absolute;left:865px;top:302px;display:flex;gap:14px}
.social i{width:36px;height:36px;border-radius:50%;border:2px solid var(--ink);display:block}
</style>
</head>
<body>

<header class="site-header">
  <div class="brand"><span class="brand-dot"></span>ROVANIX</div>
  <div class="utility">
    <span class="item"><svg width="12" height="12" viewBox="0 0 12 12"><circle cx="6" cy="4" r="3" fill="#e8600c"/><rect x="1" y="7" width="10" height="5" rx="2" fill="#e8600c"/></svg>Account</span><span class="sep">|</span>
    <span class="item"><svg width="14" height="12" viewBox="0 0 14 12"><rect x="1" y="3" width="12" height="7" rx="2" fill="#e8600c"/></svg>My Trips</span><span class="sep">|</span>
    <span class="item"><svg width="12" height="12" viewBox="0 0 12 12"><path d="M2 8V6a4 4 0 0 1 8 0v2" stroke="#e8600c" stroke-width="2" fill="none"/></svg>Support</span>
  </div>
  <div class="call">
    <span class="call-icon"><svg width="18" height="18" viewBox="0 0 24 24"><path d="M6.6 10.8a15 15 0 0 0 6.6 6.6l2.2-2.2a1 1 0 0 1 1-.25 11.4 11.4 0 0 0 3.6.57 1 1 0 0 1 1 1V20a1 1 0 0 1-1 1A17 17 0 0 1 3 4a1 1 0 0 1 1-1h3.5a1 1 0 0 1 1 1c0 1.25.2 2.45.57 3.57a1 1 0 0 1-.25 1z" fill="#fff"/></svg></span>
    Calls Us At: <b>180 041 7719</b>
  </div>
  <nav class="main-nav">
    <span class="active">Home</span><span>Flights</span><span>Destinations</span><span>Hotels</span><span>Why Us</span><span>Locations</span><span>Contact Us</span>
  </nav>
</header>

<section class="hero" role="img" aria-label="Photo of a hiker with a backpack looking over mountains at sunset">
  <div class="search-panel">
    <div class="tabs">
      <div class="tab" style="width:105px">✈ Flights</div>
      <div class="tab" style="width:110px">▦ Hotels</div>
      <div class="tab active" style="width:202px">▣ Vacation Packages</div>
      <div class="tab" style="width:89px">▭ Bus</div>
      <div class="tab" style="width:176px">▤ Resort Locations</div>
      <div class="tab" style="width:186px">▥ Visa Requirement</div>
    </div>
    <div class="tab-rule"></div>
    <div class="subtabs">
      <div class="subtab active">Flight + Hotel</div>
      <div class="subtab">Flight + Hotel + Car</div>
      <div class="subtab">Flight + Car</div>
      <div class="subtab" style="border:none">Hotel + Car</div>
    </div>

    <div class="field-label" style="left:32px;top:178px">Flying from</div>
    <div class="field-label" style="left:347px;top:178px">Flying to</div>
    <div class="field-label" style="left:665px;top:178px">Departing</div>
    <div class="field" style="left:32px;top:205px;width:303px">⚲ City or airport</div>
    <div class="field" style="left:347px;top:205px;width:303px">⚲ City or airport</div>
    <div class="field" style="left:665px;top:205px;width:303px">▦ mm/dd/yy</div>

    <div class="field-label" style="left:32px;top:271px">Returning</div>
    <div class="field-label" style="left:347px;top:271px">Rooms</div>
    <div class="field-label" style="left:463px;top:271px">Adults (18+)</div>
    <div class="field-label" style="left:606px;top:271px">Children (0-17)</div>
    <div class="field" style="left:32px;top:300px;width:303px">▦ mm/dd/yy</div>
    <div class="select" style="left:347px;top:300px;width:99px">1<span>⌄</span></div>
    <div class="select" style="left:463px;top:300px;width:129px">1<span>⌄</span></div>
    <div class="select" style="left:606px;top:300px;width:131px">1<span>⌄</span></div>

    <div class="check"><i></i>I only need a hotel for part of my stay</div>
    <div class="select" style="left:32px;top:413px;width:166px;font-size:13px">Economy/Coach<span>⌄</span></div>
    <div class="btn-search">Search</div>
    <div class="save-note">Save up to $500</div>
    <div class="panel-rule"></div>
  </div>
</section>

<section class="welcome">
  <h2 class="section-title">WELCOME TO ROVANIX</h2>
  <p class="lead">Save Up to 50% on Business, First Class, Premium Economy, and Economy Flights!</p>
  <p class="copy" style="top:140px">Nemo enim ipsam voluptatem quia voluptas sit aspernatur aut odit aut fugit, sed quia consequuntur magni dolores eos qui ratione voluptatem sequi nesciunt. Neque porro quisquam est, qui dolorem ipsum quia dolor sit amet, consectetur, adipisci velit, sed quia non numquam eius modi tempora.</p>
  <p class="copy" style="top:228px">Sed ut perspiciatis unde omnis iste natus error sit voluptatem accusantium doloremque laudantium, totam rem aperiam, eaque ipsa quae ab illo inventore veritatis et quasi.</p>
  <div class="btn btn-primary" style="left:99px;top:301px;width:110px">Read More</div>
  <div class="btn btn-outline" style="left:226px;top:301px;width:112px">Contact Us</div>
  <div class="luggage" role="img" aria-label="Illustration of stacked orange and green suitcases"></div>
</section>

<section class="deals" role="region" aria-label="Top deals">
  <div class="abs" style="inset:0;background:linear-gradient(180deg,rgba(70,80,95,.35),rgba(0,0,0,0))" role="img" aria-label="Dim background photo of a city street"></div>
  <h2 class="title">OUR TOP DEALS</h2>
  <p class="sub">Save Up to 50% on Business, First Class, Premium Economy, and Economy Flights!</p>
  <div class="arrow-btn" style="left:99px"><svg width="36" height="36" viewBox="0 0 36 36"><path d="M21 11l-7 7 7 7" stroke="#fff" stroke-width="2.5" fill="none"/></svg></div>
  <div class="arrow-btn" style="left:1061px"><svg width="36" height="36" viewBox="0 0 36 36"><path d="M15 11l7 7-7 7" stroke="#fff" stroke-width="2.5" fill="none"/></svg></div>

  <div class="deal" style="left:97px">
    <div class="deal-photo" role="img" aria-label="Photo of friends sharing a meal while travelling" style="background:linear-gradient(160deg,#c9b79a,#8c6a4f 60%,#5a4a3c)"><div class="deal-label hot">CHEAP FLIGHTS</div></div>
    <p class="deal-text">Nemo enim ipsam voluptatem quia voluptas sit aspernatur aut odit aut fugit, sed quia consequuntur.</p>
    <div class="deal-foot"><span class="stars">★★★☆☆</span><span class="book hot">BOOK NOW</span></div>
  </div>
  <div class="deal" style="left:352px">
    <div class="deal-photo" role="img" aria-label="Photo of a couple with famous city landmarks" style="background:linear-gradient(180deg,#8fb6d8,#c9d3c4 45%,#6e8a4a 75%,#4e5a3a)"><div class="deal-label">VISA REQUIREMENT</div></div>
    <p class="deal-text">Nemo enim ipsam voluptatem quia voluptas sit aspernatur aut odit aut fugit, sed quia consequuntur.</p>
    <div class="deal-foot"><span class="stars">★★★☆☆</span><span class="book">BOOK NOW</span></div>
  </div>
  <div class="deal" style="left:606px">
    <div class="deal-photo" role="img" aria-label="Photo of a hiker celebrating on a mountain top" style="background:linear-gradient(180deg,#3f7fc4,#a9c8e6 45%,#7b7f86 70%,#4a4e55)"><div class="deal-label hot">VACATION PACKAGES</div></div>
    <p class="deal-text">Nemo enim ipsam voluptatem quia voluptas sit aspernatur aut odit aut fugit, sed quia consequuntur.</p>
    <div class="deal-foot"><span class="stars">★★★☆☆</span><span class="book">BOOK NOW</span></div>
  </div>
  <div class="deal" style="left:861px">
    <div class="deal-photo" role="img" aria-label="Photo of a cyclist resting in a mountain valley" style="background:linear-gradient(180deg,#5b8fd0,#dfe6ee 40%,#8a8f7a 65%,#5a5a4a)"><div class="deal-label">RESORT LOCATIONS</div></div>
    <p class="deal-text">Nemo enim ipsam voluptatem quia voluptas sit aspernatur aut odit aut fugit, sed quia consequuntur.</p>
    <div class="deal-foot"><span class="stars">★★★☆☆</span><span class="book">BOOK NOW</span></div>
  </div>
</section>

<section class="destinations">
  <h2 class="section-title center-title" style="top:68px">POPULAR DESTINATIONS</h2>
  <p class="center-sub" style="top:118px">We Fly To and From Anywhere in the World!</p>

  <div class="tile" style="left:99px;top:177px;background:linear-gradient(180deg,#3a6fa8,#27496e 60%,#1b2d40)" role="img" aria-label="Photo of Sydney harbour"><h3>Australia</h3><p>From $ 475</p></div>
  <div class="tile" style="left:301px;top:177px;background:linear-gradient(180deg,#6f8fb0,#3d5670 55%,#25323f)" role="img" aria-label="Photo of a Canadian city skyline"><h3>Canada</h3><p>From $ 475</p></div>
  <div class="tile" style="left:505px;top:177px;background:linear-gradient(180deg,#4f88c0,#3a8a9a 55%,#6a6a4a)" role="img" aria-label="Photo of a Caribbean beach with palms"><h3>Caribbean</h3><p>From $ 475</p></div>
  <div class="tile" style="left:709px;top:177px;background:linear-gradient(180deg,#7a8898,#4e5660 55%,#2f3238)" role="img" aria-label="Photo of a Far East city harbour"><h3>Far East</h3><p>From $ 475</p></div>
  <div class="tile" style="left:913px;top:177px;background:linear-gradient(180deg,#3d74b3,#2aa4b2 60%,#1d6d7a)" role="img" aria-label="Photo of a tropical Indian Ocean lagoon"><h3>Indian Ocean</h3><p>From $ 475</p></div>

  <div class="tile" style="left:99px;top:337px;background:linear-gradient(180deg,#4a7d4a,#3c6a35 55%,#2a3f20)" role="img" aria-label="Photo of a Middle East palace and gardens"><h3>Middle East</h3><p>From $ 475</p></div>
  <div class="tile" style="left:301px;top:337px;background:linear-gradient(180deg,#2e4a3a,#1f3a2c 55%,#15241b)" role="img" aria-label="Photo of a New Zealand lake and mountains"><h3>New Zealand</h3><p>From $ 475</p></div>
  <div class="tile" style="left:505px;top:337px;background:linear-gradient(180deg,#25324a,#2c3a55 50%,#5a4a3a)" role="img" aria-label="Photo of a South African city at dusk"><h3>South Africa</h3><p>From $ 475</p></div>
  <div class="tile" style="left:709px;top:337px;background:linear-gradient(180deg,#3a4a66,#4a4e58 55%,#2a2a30)" role="img" aria-label="Photo of a South American city view"><h3>South America</h3><p>From $ 475</p></div>
  <div class="tile" style="left:913px;top:337px;background:linear-gradient(180deg,#1c2a55,#1e2a48 55%,#6a4a2a)" role="img" aria-label="Photo of a US city skyline at night"><h3>USA</h3><p>From $ 475</p></div>
</section>

<section class="why">
  <h2 class="section-title center-title" style="top:62px">WHY CHOOSE ROVANIX</h2>
  <p class="center-sub" style="top:114px">We have years of experience with getting people the best deal on their flights.</p>

  <div class="feature" style="left:99px">
    <div class="feature-icon" style="background:var(--orange);border:3px solid #f3c4a4">
      <svg width="48" height="48" viewBox="0 0 24 24"><path d="M21 13v-2l-8-4V3.5a1.5 1.5 0 0 0-3 0V7l-8 4v2l8-2.5V16l-2 1.5V19l3.5-1 3.5 1v-1.5L13 16v-5.5z" fill="#fff" transform="rotate(90 12 12)"/></svg>
    </div>
    <div><h4>Cheap Flights</h4><p>Nemo enim ipsam voluptatem quia voluptas sit aspernatur aut odit aut fugit.</p></div>
  </div>
  <div class="feature" style="left:448px">
    <div class="feature-icon" style="background:#1d1d1f;border:3px solid #bbb">
      <svg width="48" height="48" viewBox="0 0 48 48"><circle cx="24" cy="17" r="8" fill="none" stroke="#fff" stroke-width="2.5"/><text x="24" y="21.5" text-anchor="middle" font-size="11" font-weight="700" fill="#fff" font-family="Open Sans, sans-serif">$</text><path d="M8 32h8l6 3h8a2 2 0 0 1 0 4H20M8 40h8l8 2 14-6a2 2 0 0 0-2-3" fill="none" stroke="#fff" stroke-width="2.5"/></svg>
    </div>
    <div><h4>Fantastic Savings</h4><p>Nemo enim ipsam voluptatem quia voluptas sit aspernatur aut odit aut fugit.</p></div>
  </div>
  <div class="feature" style="left:804px">
    <div class="feature-icon" style="background:var(--orange);border:3px solid #f3c4a4">
      <svg width="48" height="48" viewBox="0 0 48 48"><path d="M18 12h12l-3 5h-6z" fill="#fff"/><path d="M20 18h8c8 4 11 12 9 18-1 4-5 6-13 6s-12-2-13-6c-2-6 1-14 9-18z" fill="#fff"/><text x="24" y="36" text-anchor="middle" font-size="14" font-weight="700" fill="#e8600c" font-family="Open Sans, sans-serif">$</text></svg>
    </div>
    <div><h4>Different Rates</h4><p>Nemo enim ipsam voluptatem quia voluptas sit aspernatur aut odit aut fugit.</p></div>
  </div>
</section>

<footer class="site-footer">
  <div class="footer-brand"><span class="brand-dot"></span>ROVANIX</div>
  <div class="contact-row">
    <span><i class="ring"><svg width="18" height="14" viewBox="0 0 18 14"><rect x="1" y="1" width="16" height="12" rx="1" fill="none" stroke="#222" stroke-width="1.6"/><path d="M1 2l8 6 8-6" fill="none" stroke="#222" stroke-width="1.6"/></svg></i>info@Rovanix.com</span>
    <span><i class="ring"><svg width="16" height="16" viewBox="0 0 24 24"><path d="M6.6 10.8a15 15 0 0 0 6.6 6.6l2.2-2.2a1 1 0 0 1 1-.25 11.4 11.4 0 0 0 3.6.57 1 1 0 0 1 1 1V20a1 1 0 0 1-1 1A17 17 0 0 1 3 4a1 1 0 0 1 1-1h3.5a1 1 0 0 1 1 1c0 1.25.2 2.45.57 3.57a1 1 0 0 1-.25 1z" fill="#222"/></svg></i>180 041 7719</span>
  </div>
  <nav class="footer-nav">
    <span>HOME</span><span>|</span><span>FLIGHTS</span><span>|</span><span>DESTINATIONS</span><span>|</span><span>HOTELS</span><span>|</span><span>WHY US</span><span>|</span><span>LOCATIONS</span><span>|</span><span>CONTACT US</span>
  </nav>
  <div class="footer-rule"></div>
  <p class="copyright">Copyright © 2017 Rovanix. All Right Reserved</p>
  <div class="social" aria-label="Social links"><i></i><i></i><i></i><i></i><i></i></div>
</footer>

</body>
</html>
```